Halvern Roofing & Waterproofing HOA & Commercial Roofing Specialists

FRONT COVER (Panel 1)
Halvern Roofing & Waterproofing
HOA & Commercial Roofing Specialists
Protecting Communities.
Preserving Property Value.
Delivering Long-Term Solutions.
📍 Serving Orange County & Surrounding Areas
INSIDE LEFT PANEL (Panel 2)
Who We Are
Halvern Roofing & Waterproofing is a trusted HOA and commercial roofing specialist serving Orange County and surrounding areas. We understand the unique needs of homeowner associations, property managers, and commercial properties—delivering reliable service, clear communication, and long-lasting results.
✔ HOA-Focused Expertise
✔ Licensed & Insured
✔ Emergency Response Available
✔ Quality Workmanship You Can Trust
INSIDE MIDDLE PANEL (Panel 3)
Roofing Services
HOA & Commercial Roofing
• Emergency roof tarping & repairs — Starting at $550
• Small & large roof repairs
• Chimney cap and spark arrestor repairs
• Preventative roof maintenance
• Roof cleaning
• Full roof replacement
We work on all roof types:
✔ Flat Roofs (Torch down, TPO, & PVC)
✔ Tile Roofs (Clay tiles, concrete tiles, and more)
✔ Shingle Roofs - KOV certified contractor
• Coating (silicone or acrylic)
No matter the size or system—we’ve got you covered.
INSIDE RIGHT PANEL (Panel 4)
Gutter Services
• Small & large gutter repairs
• Gutter cleaning & maintenance
• New gutter installation & replacement
Proper drainage protects your building—let us handle it.
BACK LEFT PANEL (Panel 5)
Deck/Balcony Waterproofing Services
• Balcony/deck maintenance
• Deck resurfacing
• Small & large deck repairs
• Full deck reconstruction
Specialized waterproofing solutions to keep decks safe, compliant, and durable.
BACK COVER (Panel 6)
Why Choose Halvern?
✔ HOA & Commercial Specialists
✔ Fully Licensed & Insured
✔ Reliable Scheduling
✔ Clear Communication
✔ Quality Materials & Craftsmanship
License Information:
C-39 Roofing Contractor
General B Contractor
License #4630257
📍 Office Location:
14 Dunmore Street, Suite J Irvine, CA 92618
📞 Contact us today for a consultation
949-372-6104 or rfp@halvernroofing.com
🌐 Serving Orange County & surrounding areas
- Gotham

```html
<!DOCTYPE html>
<html lang="en">
<head>
<meta charset="utf-8">
<title>Halvern Roofing &amp; Waterproofing – Trifold Brochure</title>
<link rel="stylesheet" href="https://fonts.googleapis.com/css2?family=Jost:ital,wght@0,300;0,400;0,500;0,600;0,700;1,400;1,600;1,700&display=swap">
<style>
:root{
  --navy:#1b5496;
  --blue:#1d5b9f;
  --sky:#4aa8dc;
  --ink:#1c2633;
  --paper:#ffffff;
  --page:#eef0f2;
  --deck-tone:#6f8b87;
  --roof-tone:#8e8f7c;
  --cover-tone:#7c7a6a;
  --membrane-tone:#dfe6ec;
  --gutter-tone:#8c8a72;
}
*{margin:0;padding:0;box-sizing:border-box}
html,body{width:1200px;height:2541px;overflow:hidden;background:var(--page)}
body{font-family:"Jost",sans-serif;color:var(--ink);position:relative}
.spread{position:absolute;left:60px;width:1096px;height:776px;background:var(--paper);box-shadow:0 6px 18px rgba(0,0,0,.35);overflow:hidden}
.spread--outside{top:42px}
.spread--inside{top:903px}
.panel{position:absolute;top:0;width:366px;height:776px;overflow:hidden}
.panel--1{left:0}.panel--2{left:365px}.panel--3{left:730px}
.panel svg.bg{position:absolute;left:0;top:0;width:366px;height:776px}
.t{position:absolute}
h2,h3{font-weight:700;line-height:1}
.dots{position:absolute;background-image:radial-gradient(circle,var(--sky) 1.4px,transparent 1.8px);background-size:12px 12px}
ul{list-style:none}
.bullets li{position:relative;padding-left:20px}
.bullets li::before{content:"";position:absolute;left:3px;top:.55em;width:5px;height:5px;border-radius:50%;background:currentColor}
.checks li{position:relative;padding-left:26px}
.checks li svg{position:absolute;left:0;top:.2em;width:15px;height:13px}
.rule{position:absolute;height:2px;background:var(--sky)}

/* deck panel */
.deck-icon{position:absolute;left:32px;top:428px;width:74px;height:70px;border:2px solid var(--navy);border-radius:6px;background:#eaf3fa}
.deck-title{left:126px;top:413px;font-size:31px;color:var(--navy);line-height:31px}
.deck-list{left:40px;top:523px;font-size:17px;line-height:21.5px;color:var(--ink)}
.deck-note{left:37px;top:624px;width:312px;font-size:13px;line-height:16.5px;font-style:italic}

/* back cover */
.why-title{left:37px;top:54px;font-size:30px;color:#fff}
.why-list{left:42px;top:103px;font-size:13px;line-height:20.5px;color:#fff;font-weight:300}
.lic-title{left:37px;top:243px;font-size:29px;color:#fff}
.lic-lines{left:37px;top:279px;font-size:16px;line-height:25.5px;color:#fff;font-weight:300}
.lic-lines b{font-weight:700}
.office{left:94px;top:451px;font-size:15px;line-height:16.5px;color:var(--ink)}
.office strong{display:block;font-size:16px;font-weight:600;margin-bottom:2px}
.schedule{left:37px;top:542px;font-size:19px;line-height:19px;color:var(--ink);font-weight:600}
.contact-row{left:76px;font-size:13.5px;line-height:16px;color:var(--ink)}
.contact-row strong{display:block;font-weight:600;font-size:14px}
.mini-brand{left:262px;top:640px;font-size:19px;font-weight:700;color:#fff;letter-spacing:.5px}
.serving{left:37px;top:694px;width:290px;font-size:13.5px;line-height:14.5px;font-style:italic;font-weight:700;color:#fff}

/* front cover */
.brand{left:24px;top:66px;font-size:36px;font-weight:700;color:var(--ink);letter-spacing:1px}
.cover-title{left:21px;top:146px;font-size:29.5px;line-height:35px;color:#1b5aa3;font-weight:700}
.tagline{left:21px;top:307px;font-size:16px;line-height:17px;font-weight:700;color:var(--ink)}
.cover-area{left:21px;top:370px;font-size:16px;line-height:18px;font-style:italic;color:var(--ink)}
.cover-caption{left:24px;top:712px;width:320px;font-size:11px;line-height:12px;font-style:italic;font-weight:700;color:#fff}

/* who we are */
.who-title{left:25px;top:58px;font-size:29px;color:var(--navy)}
.who-text{left:25px;width:305px;font-size:14.5px;line-height:18px;color:var(--ink)}
.who-list{left:25px;top:350px;font-size:13.5px;line-height:20.5px}

/* roofing services */
.roof-title{left:15px;top:226px;font-size:44px;line-height:37px;color:var(--navy)}
.roof-sub{left:15px;top:312px;font-size:20px;font-weight:600;color:var(--ink)}
.roof-list{left:19px;top:343px;font-size:12px;line-height:14.6px}
.roof-list li{padding-left:17px}
.types-title{left:15px;top:449px;font-size:21.5px;font-weight:600;color:var(--ink)}
.types{position:absolute;left:21px;top:477px;width:314px}
.types li{display:flex;align-items:center;height:61px;border-bottom:2px solid var(--navy);font-size:14px;font-weight:600;line-height:17px;color:var(--ink)}
.types li svg{flex:none;width:52px;height:34px;margin-right:20px}
.types-note{left:22px;top:724px;font-size:12px;font-style:italic;font-weight:700;color:var(--navy)}

/* gutter */
.gutter-icon{position:absolute;left:22px;top:62px;width:60px;height:58px}
.gutter-title{left:100px;top:58px;font-size:29px;line-height:32px;color:#fff}
.gutter-list{left:32px;top:132px;font-size:15px;line-height:19.5px;color:#fff;width:245px;font-weight:300}
.gutter-note{left:26px;top:222px;width:268px;font-size:13px;line-height:16.5px;font-style:italic;color:#fff;font-weight:300}
</style>
</head>
<body>

<svg width="0" height="0" style="position:absolute">
  <symbol id="tick" viewBox="0 0 15 13"><path d="M1 7l4 4.5L14 1" fill="none" stroke="currentColor" stroke-width="2.4" stroke-linecap="round" stroke-linejoin="round"/></symbol>
</svg>

<section class="spread spread--outside">

  <article class="panel panel--1 deck-panel">
    <svg class="bg" viewBox="0 0 366 776" aria-hidden="true">
      <rect width="366" height="470" fill="var(--deck-tone)" role="img" aria-label="Photo of a freshly coated balcony deck"/>
      <polygon points="0,340 0,776 366,776 366,300" fill="var(--sky)"/>
      <polygon points="0,445 258,322 366,388 366,776 0,776" fill="var(--paper)"/>
    </svg>
    <div class="dots" style="left:286px;top:334px;width:52px;height:52px"></div>
    <div class="deck-icon" role="img" aria-label="Deck and balcony icon"></div>
    <h2 class="t deck-title">Deck &amp;<br>Balcony<br>Waterproofing</h2>
    <ul class="t bullets deck-list">
      <li>Balcony &amp; deck maintenance</li>
      <li>Deck resurfacing</li>
      <li>Small &amp; large deck repairs</li>
      <li>Full deck reconstruction</li>
    </ul>
    <p class="t deck-note">We provide specialized waterproofing solutions designed to keep decks safe, compliant, and durable—helping prevent costly structural damage while extending the life of your property.</p>
  </article>

  <article class="panel panel--2 back-cover">
    <svg class="bg" viewBox="0 0 366 776" aria-hidden="true">
      <rect width="366" height="776" fill="var(--sky)"/>
      <polygon points="0,0 366,0 366,355 185,430 0,355" fill="var(--blue)"/>
      <polygon points="366,320 366,380 300,350" fill="var(--paper)"/>
    </svg>
    <h2 class="t why-title">Why Choose Halvern?</h2>
    <ul class="t checks why-list">
      <li><svg><use href="#tick"/></svg>HOA &amp; Commercial Specialists</li>
      <li><svg><use href="#tick"/></svg>Fully Licensed &amp; Insured</li>
      <li><svg><use href="#tick"/></svg>Reliable Scheduling</li>
      <li><svg><use href="#tick"/></svg>Clear Communication</li>
      <li><svg><use href="#tick"/></svg>Quality Materials &amp; Craftsmanship</li>
    </ul>
    <div class="rule" style="left:42px;top:227px;width:40px"></div>
    <h2 class="t lic-title">License Information</h2>
    <p class="t lic-lines">C-39 Roofing Contractor<br>General B Contractor<br>License <b>#4630257</b></p>

    <svg class="t" style="left:36px;top:455px" width="38" height="40" viewBox="0 0 38 40" aria-hidden="true">
      <path d="M19 2a14 14 0 0 0-14 14c0 10 14 22 14 22s14-12 14-22A14 14 0 0 0 19 2z" fill="var(--navy)"/>
      <circle cx="19" cy="16" r="5.5" fill="none" stroke="var(--sky)" stroke-width="2.5"/>
    </svg>
    <p class="t office"><strong>Office Location</strong>14 Dunmore Street, Suite J<br>Irvine, CA 92618</p>
    <div class="rule" style="left:37px;top:523px;width:40px;background:#fff"></div>
    <h3 class="t schedule">Schedule Your Consultation<br>Today</h3>
    <div class="dots" style="left:322px;top:532px;width:44px;height:54px;background-image:radial-gradient(circle,#fff 1.4px,transparent 1.8px)"></div>

    <svg class="t" style="left:37px;top:600px" width="26" height="26" viewBox="0 0 24 24" aria-hidden="true">
      <path d="M6.6 10.8a15 15 0 0 0 6.6 6.6l2.2-2.2a1 1 0 0 1 1-.25 11.4 11.4 0 0 0 3.6.57 1 1 0 0 1 1 1V20a1 1 0 0 1-1 1A17 17 0 0 1 3 4a1 1 0 0 1 1-1h3.5a1 1 0 0 1 1 1c0 1.25.2 2.45.57 3.57a1 1 0 0 1-.25 1z" fill="var(--navy)"/>
    </svg>
    <p class="t contact-row" style="top:596px"><strong>Phone</strong>949-372-6104</p>
    <svg class="t" style="left:35px;top:646px" width="30" height="22" viewBox="0 0 30 22" aria-hidden="true">
      <rect x="1.5" y="1.5" width="27" height="19" fill="none" stroke="var(--navy)" stroke-width="2.2"/>
      <path d="M1.5 1.5L15 12 28.5 1.5M1.5 20.5l10-9M28.5 20.5l-10-9" fill="none" stroke="var(--navy)" stroke-width="2.2"/>
    </svg>
    <p class="t contact-row" style="top:639px"><strong>Email</strong>rfp@halvernroofing.com</p>
    <p class="t mini-brand">HALVERN</p>
    <p class="t serving">Serving Orange County &amp; surrounding areas</p>
  </article>

  <article class="panel panel--3 front-cover">
    <svg class="bg" viewBox="0 0 366 776" aria-hidden="true">
      <rect y="360" width="366" height="416" fill="var(--cover-tone)" role="img" aria-label="Photo of a roofer in safety harness working on a tile roof"/>
      <polygon points="0,0 366,0 366,345 110,465 0,410" fill="var(--paper)"/>
      <polygon points="366,345 366,420 225,410" fill="var(--sky)"/>
      <polygon points="0,400 0,440 55,438" fill="var(--sky)"/>
    </svg>
    <div class="dots" style="left:282px;top:55px;width:52px;height:52px"></div>
    <p class="t brand">HALVERN</p>
    <h1 class="t cover-title">Halvern Roofing &amp;<br>Waterproofing<br>HOA &amp; Commercial<br>Roofing Specialists</h1>
    <div class="rule" style="left:21px;top:296px;width:40px"></div>
    <p class="t tagline">Protecting Communities.<br>Preserving Property Value.<br>Delivering Long-Term Solutions.</p>
    <p class="t cover-area">Proudly Serving Orange<br>County &amp; Surrounding Areas</p>
    <p class="t cover-caption">Reliable roofing, waterproofing, and exterior solutions for homeowner associations, property managers, and commercial properties.</p>
  </article>
</section>

<section class="spread spread--inside">

  <article class="panel panel--1 who-we-are">
    <svg class="bg" viewBox="0 0 366 776" aria-hidden="true">
      <rect y="440" width="366" height="336" fill="var(--membrane-tone)" role="img" aria-label="Photo of a white coated commercial flat roof"/>
      <polygon points="0,0 366,0 366,440 110,510 0,455" fill="var(--paper)"/>
      <polygon points="366,388 366,470 230,468" fill="var(--blue)"/>
    </svg>
    <div class="dots" style="left:78px;top:0;width:52px;height:40px"></div>
    <div class="dots" style="left:296px;top:330px;width:52px;height:52px"></div>
    <h2 class="t who-title">Who We Are</h2>
    <p class="t who-text" style="top:102px">Halvern Roofing &amp; Waterproofing is a trusted HOA and commercial roofing contractor serving Orange County and surrounding areas. We specialize in protecting multi-unit and commercial properties through dependable service, clear communication, and long-lasting results.</p>
    <p class="t who-text" style="top:247px">We understand the unique demands of HOA boards and property managers—and we deliver solutions that minimize disruption while maximizing property value.</p>
    <ul class="t checks who-list" style="color:var(--ink)">
      <li><svg style="color:var(--navy)"><use href="#tick"/></svg>HOA-Focused Expertise</li>
      <li><svg style="color:var(--navy)"><use href="#tick"/></svg>Fully Licensed &amp; Insured</li>
      <li><svg style="color:var(--navy)"><use href="#tick"/></svg>Emergency Response Available</li>
      <li><svg style="color:var(--navy)"><use href="#tick"/></svg>Quality Workmanship You Can Trust</li>
    </ul>
  </article>

  <article class="panel panel--2 roofing-services">
    <svg class="bg" viewBox="0 0 366 776" aria-hidden="true">
      <rect width="366" height="340" fill="var(--roof-tone)" role="img" aria-label="Aerial photo of a townhome community during roof replacement"/>
      <polygon points="0,232 110,180 366,330 366,776 0,776" fill="var(--paper)"/>
      <polygon points="258,272 366,205 366,332" fill="var(--blue)"/>
    </svg>
    <h2 class="t roof-title">Roofing<br>Services</h2>
    <h3 class="t roof-sub">HOA &amp; Commercial Roofing</h3>
    <ul class="t bullets roof-list">
      <li>Emergency roof tarping &amp; repairs — starting at $550</li>
      <li>Small &amp; large roof repairs</li>
      <li>Chimney cap &amp; spark arrestor repairs</li>
      <li>Preventative roof maintenance programs</li>
      <li>Roof cleaning</li>
      <li>Full roof replacement</li>
    </ul>
    <h3 class="t types-title">We Service All Roof Types:</h3>
    <ul class="types">
      <li>
        <svg viewBox="0 0 52 34" aria-hidden="true" fill="none" stroke="var(--navy)" stroke-width="1.6"><rect x="3" y="10" width="46" height="20"/><path d="M3 10h46M8 15h4M16 15h4M24 15h4M32 15h4M40 15h4M8 21h4M16 21h4M32 21h4M40 21h4M24 30v-9h5v9"/></svg>
        Flat Roofs (Torch Down, TPO, PVC)
      </li>
      <li>
        <svg viewBox="0 0 52 34" aria-hidden="true" fill="none" stroke="var(--navy)" stroke-width="1.6"><path d="M6 16L26 3l20 13M10 14v17h32V14M22 31v-9h8v9M14 18h5v4h-5zM33 18h5v4h-5z"/></svg>
        Tile Roofs (Clay, Concrete &amp; More)
      </li>
      <li>
        <svg viewBox="0 0 52 34" aria-hidden="true" fill="none" stroke="var(--navy)" stroke-width="1.6"><path d="M3 28l8-18h24l-8 18zM7 19h24M5 24h24M13 10l-8 18M21 10l-8 18M29 10l-8 18"/><circle cx="41" cy="20" r="7"/><path d="M38 20l2.5 2.5L45 17"/></svg>
        Shingle Roofs — KOV Certified<br>Contractor
      </li>
      <li>
        <svg viewBox="0 0 52 34" aria-hidden="true" fill="none" stroke="var(--navy)" stroke-width="1.6"><path d="M6 22L28 10l10 6M10 20v10h20V14"/><rect x="34" y="2" width="14" height="6" rx="1"/><path d="M41 8v8"/><circle cx="18" cy="29" r="1.2" fill="var(--navy)"/><circle cx="24" cy="28" r="1.2" fill="var(--navy)"/></svg>
        Roof Coatings (Silicone or Acrylic)
      </li>
    </ul>
    <p class="t types-note">No matter the size or system—we’ve got you covered.</p>
    <div class="dots" style="left:322px;top:738px;width:44px;height:30px"></div>
  </article>

  <article class="panel panel--3 gutter-services">
    <svg class="bg" viewBox="0 0 366 776" aria-hidden="true">
      <rect y="250" width="366" height="526" fill="var(--gutter-tone)" role="img" aria-label="Photo of a roofer cleaning a gutter on a gravel roof"/>
      <polygon points="0,0 366,0 366,272 110,310 0,305" fill="var(--blue)"/>
      <polygon points="366,272 366,312 318,290" fill="var(--sky)"/>
    </svg>
    <svg class="gutter-icon" viewBox="0 0 60 58" aria-hidden="true" fill="#fff">
      <path d="M0 0h60v6c0 5-4 9-9 9H9c-5 0-9-4-9-9z"/>
      <path d="M28 15h12v22c0 4-2 7-6 9l-6 3v9h-8V44l8-5z"/>
    </svg>
    <h2 class="t gutter-title">Gutter<br>Services</h2>
    <div class="dots" style="left:292px;top:112px;width:52px;height:52px"></div>
    <ul class="t bullets gutter-list">
      <li>Small &amp; large gutter repairs</li>
      <li>Gutter cleaning &amp; maintenance</li>
      <li>New gutter installation &amp; replacement</li>
    </ul>
    <p class="t gutter-note">Proper drainage protects your building’s foundation and exterior. Let our team ensure your gutter system performs reliably year-round.</p>
  </article>
</section>

</body>
</html>
```